Packaging Design: Logo/Bottle Design for New Botanical Cocktail Brand

We are a new start up, looking to create a new line of Ready to drink Cocktails. The brand name is Verdance Garden Spritzers, infused with fruit, herb, and floral botanicals grown on our farm in New Hampshire. Flavors will include: Herb flavored with cilantro, Berry- flavored with Ridgeglow Berry, Citrus flavored with lemon Verbena & lemon balm, Pear flavored with Quillon pear, Cucumber & Mint. We need a logo and a label design. There are 2 possible bottles to choose from.

Designer has complete freedom with everything! From fonts and colors to bottle caps and closures. Please view the pinterest link for inspirational bottle designs. https://www.pinboardia.com/dellacravitz/garden-spritzers/

Reason: I am extending the deadline for my project to allow more designers to submit their designs.

Target Market(s)

Female 21 to 48 years old. College educated and professional. The type of person that has a passion for a cause and eats and shops local. People that respect an artisan quality product, hand made by a master craftsman.

Industry/Entity Type

Floral

Requirements
Must have
• Clear Bottle, see options attached. You may also choose your own BUT WE MUST SEE THE LOGO AND IMAGERY ON A BOTTLE
• Logo Design: "Verdance Garden Spritzers"
• Label: We can have front and back, or one continuous label. We are open to painted designs.
• The label must contain the following text in quotes:
• Product Name: " Verdance Garden Spritzers "
• "15% Alc. by Vol. (30 proof)"
• "750 mL"
• "Handcrafted and Bottled by Hollowmere Stillbrook Farm and Distillery
• Fernhollow, Greenvale-USA"
• The following Text must be in all caps and 3mm in height:
• "Government Warning: (1) According to the Surgeon General, women should not drink alcoholic beverages during pregnancy because of the risk of birth defects. (2) Consumption of alcoholic beverages impairs your ability to drive a car or operate machinery and may cause health problems."
• Must be a space for a bar code: .75 in height by 1.25 in length.
• “www.hollowmerestillbrook.com”
• Must Have the following Statement:
• Infused with fruit, herb, and floral botanicals and sweetened with stevia. Serve cold over ice.
Nice to have
• Antique or vintage botanical illustrations
• https://www.pinboardia.com/dellacravitz/garden-spritzers/
• check out the board for inspiration.
• Think artisanal small batch spirits that are ready to drink out of the bottle. Refreshing flavors just pour over ice and add herb leaves.
• You can use images by doing a search here.
• http://archv.plantrec.example.org/archv/search.xhtml?start=0&collectionFacet=Orchard+Painted+Plate+Archive

```html
<!DOCTYPE html>
<html lang="en">
<head>
<meta charset="utf-8">
<title>Verdance Garden Spritzers – Front and Back Labels</title>
<link rel="stylesheet" href="https://fonts.googleapis.com/css2?family=Josefin+Sans:wght@300;400&family=Italianno&display=swap">
<style>
  :root {
    --backdrop: #e8e8ea;
    --label: #e3e98c;
    --ink: #3a3632;
    --ink-soft: #5f5c4a;
    --dash: #8f8d6a;
    --fruit-light: #eef27a;
    --fruit-mid: #c9d94a;
    --leaf: #7f9a3a;
    --barcode-space: #3d3833;
  }
  * { margin: 0; padding: 0; box-sizing: border-box; }
  html, body {
    width: 1181px;
    height: 1200px;
    overflow: hidden;
    background: var(--backdrop);
  }
  .canvas {
    position: relative;
    width: 1181px;
    height: 1200px;
  }
  .label {
    position: absolute;
    top: 440px;
    width: 216px;
    height: 607px;
    color: var(--ink);
    font-family: "Josefin Sans", sans-serif;
    font-weight: 300;
  }
  .label--front { left: 184px; }
  .label--back { left: 796px; }
  .label__shape {
    position: absolute;
    inset: 0;
    width: 216px;
    height: 607px;
  }
  .wordmark {
    position: absolute;
    top: 24px;
    left: 0;
    width: 216px;
    text-align: center;
    color: var(--ink);
    line-height: 1;
  }
  .wordmark__top { font-size: 11px; letter-spacing: 1px; }
  .wordmark__main { font-size: 25px; margin: 3px 0 2px; }
  .wordmark__bottom { font-size: 11px; letter-spacing: 1px; }
  .botanical-art {
    position: absolute;
    top: 96px;
    left: 10px;
    width: 196px;
    height: 118px;
  }
  .statement {
    position: absolute;
    top: 340px;
    left: 46px;
    width: 124px;
    text-align: center;
    font-family: "Italianno", cursive;
    font-size: 19px;
    line-height: 18px;
  }
  .volume {
    position: absolute;
    top: 512px;
    left: 0;
    width: 216px;
    text-align: center;
    font-size: 10px;
    line-height: 15px;
  }
  .producer {
    position: absolute;
    top: 95px;
    left: 26px;
    width: 164px;
    text-align: center;
    font-size: 8.5px;
    line-height: 11px;
    color: var(--ink-soft);
  }
  .producer__url { display: block; margin-bottom: 2px; }
  .warning {
    position: absolute;
    top: 150px;
    left: 32px;
    width: 152px;
    text-align: center;
    font-size: 13px;
    line-height: 15.5px;
    text-transform: uppercase;
  }
  .barcode-space {
    position: absolute;
    top: 553px;
    left: 30px;
    width: 156px;
    height: 73px;
    background: var(--barcode-space);
  }
</style>
</head>
<body>
<main class="canvas">

  <section class="label label--front" aria-label="Front label">
    <svg class="label__shape" viewBox="0 0 216 607" aria-hidden="true">
      <path d="M0,108 A108,108 0 0 1 216,108 L188,607 L28,607 Z" fill="var(--label)"/>
      <path d="M9,108 A99,99 0 0 1 207,108 L180,598 L36,598 Z" fill="none" stroke="var(--dash)" stroke-width="0.8" stroke-dasharray="2 2"/>
    </svg>

    <div class="wordmark">
      <div class="wordmark__top">VERDANCE</div>
      <div class="wordmark__main">Garden</div>
      <div class="wordmark__bottom">SPRITZERS</div>
    </div>

    <svg class="botanical-art" viewBox="0 0 196 118" role="img" aria-label="Vintage botanical illustration of a lemon with mint and lemon balm leaves">
      <defs>
        <radialGradient id="fruitTone" cx="45%" cy="40%" r="60%">
          <stop offset="0%" stop-color="var(--fruit-light)"/>
          <stop offset="70%" stop-color="var(--fruit-mid)"/>
          <stop offset="100%" stop-color="var(--leaf)"/>
        </radialGradient>
      </defs>
      <ellipse cx="98" cy="60" rx="92" ry="52" fill="url(#fruitTone)" opacity="0.85"/>
    </svg>

    <p class="statement">Infused with fruit, herb, and floral botanicals and sweetened with stevia. Serve cold over ice.</p>

    <p class="volume">15% Alc. by Vol.<br>(30 proof)<br>750 mL</p>
  </section>

  <section class="label label--back" aria-label="Back label">
    <svg class="label__shape" viewBox="0 0 216 607" aria-hidden="true">
      <path d="M0,108 A108,108 0 0 1 216,108 L188,607 L28,607 Z" fill="var(--label)"/>
      <path d="M9,108 A99,99 0 0 1 207,108 L180,598 L36,598 Z" fill="none" stroke="var(--dash)" stroke-width="0.8" stroke-dasharray="2 2"/>
    </svg>

    <div class="wordmark">
      <div class="wordmark__top">VERDANCE</div>
      <div class="wordmark__main">Garden</div>
      <div class="wordmark__bottom">SPRITZERS</div>
    </div>

    <p class="producer">
      <span class="producer__url">www.hollowmerestillbrook.com</span>
      Handcrafted and Bottled by Hollowmere Stillbrook Farm and Distillery - Fernhollow, Greenvale-USA
    </p>

    <p class="warning">Government Warning: (1) According to the Surgeon General, women should not drink alcoholic beverages during pregnancy because of the risk of birth defects. (2) Consumption of alcoholic beverages impairs your ability to drive a car or operate machinery and may cause health problems.</p>

    <div class="barcode-space" aria-label="Reserved space for bar code"></div>
  </section>

</main>
</body>
</html>
```